Need business card with a logo for a hearing aid sales and audiology business. We have two Hearing Instrument Specialists and one Audiologist on staff. Over 25 years in business. Locally owned and operated. Financing available. Most insurances accepted.

Summit Audio Wellness LLC
48730 W Larchmont, Suite 7
Spokane, WA 99281
509-617-2084
www.summitaudiowell.example

Manager
Tobias Kerrell HIS COHC
License #71829046

Target Market(s)

50yr old + people with a hearing loss.

Industry/Entity Type

Business

Contact Information for Business Card

48730 W Larchmont, Suite 7
Spokane, WA 99281
509-617-2084
www.summitaudiowell.example

Manager
Tobias Kerrell HIS COHC
NLVE #71829046

Font styles to use
Serif
Sans Serif

Requirements
Must have
• Business name, Tobias's name and title(s) and contact information, License #, web address

```html
<!DOCTYPE html>
<html lang="en">
<head>
<meta charset="utf-8">
<title>Summit Audio Wellness LLC — Business Card</title>
<link rel="stylesheet" href="https://fonts.googleapis.com/css2?family=Questrial&family=Source+Sans+3:wght@400;600&display=swap">
<style>
  :root {
    --stage: #000000;
    --card-front: #f3f3f3;
    --card-back: #a9cf38;
    --card-back-deep: #9fc431;
    --brand-blue: #1b4fb8;
    --label-blue: #1a5fa8;
    --ink: #2b2b2b;
    --white: #ffffff;
  }
  * { margin: 0; padding: 0; box-sizing: border-box; }
  html, body {
    width: 1200px; height: 900px; overflow: hidden;
    background: var(--stage);
  }
  .stage { position: relative; width: 1200px; height: 900px; }

  .card {
    position: absolute; top: 200px;
    width: 310px; height: 502px;
    overflow: hidden;
  }
  .card-front {
    left: 265px;
    background: var(--card-front);
    border-radius: 62px 0 62px 0;
  }
  .card-back {
    left: 641px;
    background: linear-gradient(160deg, var(--card-back) 0%, var(--card-back-deep) 100%);
    border-radius: 0 62px 0 62px;
  }

  .wordmark {
    position: absolute; left: 0; right: 0;
    text-align: center;
    font-family: "Questrial", sans-serif;
    font-weight: 400;
    letter-spacing: 1.5px;
    line-height: 1.15;
  }
  .card-front .wordmark {
    top: 160px;
    color: var(--brand-blue);
    font-size: 20px;
  }
  .brand-dot {
    display: block;
    width: 14px; height: 14px; margin: 0 auto 12px;
    border-radius: 50%;
    background: var(--brand-blue);
  }
  .card-back .wordmark {
    top: 383px;
    color: var(--white);
    font-size: 21px;
  }

  .contact {
    position: absolute; left: 27px; top: 294px;
    font-family: "Source Sans 3", sans-serif;
    color: var(--ink);
    font-size: 13.5px;
    line-height: 18px;
  }
  .person-name {
    color: var(--brand-blue);
    font-size: 17.5px; font-weight: 600;
  }
  .credentials { font-size: 13px; font-weight: 400; }
  .role { margin-top: 2px; }
  .license { margin-top: 19px; font-weight: 600; }
  .license-label { color: var(--label-blue); }
  .contact-lines { margin-top: 19px; }
  .contact-line { display: flex; align-items: center; gap: 7px; }
  .contact-line svg { width: 11px; height: 11px; flex: none; }
  .address { margin-top: 12px; }
</style>
</head>
<body>
<main class="stage">
  <section class="card card-front" aria-label="Card front">
    <div class="wordmark">
      <span class="brand-dot"></span>
      SUMMIT AUDIO<br>WELLNESS LLC
    </div>

    <div class="contact">
      <p class="person-name">Tobias Kerrell <span class="credentials">HIS COHC</span></p>
      <p class="role">Manager</p>
      <p class="license"><span class="license-label">License</span> #71829046</p>
      <div class="contact-lines">
        <p class="contact-line">
          <svg viewBox="0 0 24 24" aria-hidden="true"><path fill="#1b4fb8" d="M6.6 10.8a15.1 15.1 0 0 0 6.6 6.6l2.2-2.2c.3-.3.7-.4 1-.2 1.1.4 2.3.6 3.6.6.6 0 1 .4 1 1V20c0 .6-.4 1-1 1A17 17 0 0 1 3 4c0-.6.4-1 1-1h3.5c.6 0 1 .4 1 1 0 1.3.2 2.5.6 3.6.1.3 0 .7-.2 1z"/></svg>
          509-617-2084
        </p>
        <p class="contact-line">
          <svg viewBox="0 0 24 24" aria-hidden="true"><circle cx="12" cy="12" r="10" fill="#1b4fb8"/><path d="M2 12h20M12 2c3 3 3 17 0 20M12 2c-3 3-3 17 0 20" stroke="#f3f3f3" stroke-width="1.6" fill="none"/></svg>
          www.summitaudiowell.example
        </p>
      </div>
      <p class="address">48730 W Larchmont,<br>Suite 7 Spokane, WA 99281</p>
    </div>
  </section>

  <section class="card card-back" aria-label="Card back">
    <div class="wordmark">SUMMIT AUDIO<br>WELLNESS LLC</div>
  </section>
</main>
</body>
</html>
```